Website for Vornelix Capital, my new firm that raises money from investors to buy, build, own an...

Vornelix Capital needs a website! We are a new company with very experienced people, who invest in, own and build hotel properties, as well as apartments and other commercial real estate. We seek investors for our projects, and we provide safe, secure returns on their investment in our projects. Our new logo is designed to exhibit strength, class and security, and would like our website to continue on this theme. Our name, Vornelix, is a word-play on a Greek word “aristeia”, which means “excellence” and “a warriors finest moment of glory in war”. If you are in business, you realize that much of it is like war, with strategy and moves and opponents and competitors, and ever-changing economic conditions and threats that make business very much like war. We like to think that we are good at business (war), and so have named our company “Vornelix”, using the founders last name and the word “aristeia” combined. Another definition of "aristeia" is "performing at the peak of one's potential after a long struggle"...again, much like business in real life! The website design should exhibit financial security, smart moves, and positive growth towards a bright future.

Target Market(s)

The target market is smart and wealthy investors, with others such as brokers, cities and government agencies, lenders, sellers, partners, etc also looking at it.

Industry/Entity Type

Investment

Number of Pages Required

5+ page

Font styles to use
Sans Serif

Colors
fec214

Requirements
Must have
• Our website should have a landing page, a "about" or bio page, a projects page and a contact us page. Our new logo uses the colors black and gold, so this should be factored in to our site. The site should be simple, yet impactful and impressive. I have actually two logos, which can be mixed and interchanged in a complimentary way, each with their own unique look.
Nice to have
• I have uploaded a couple screenshots of a website i like, and the simplicity I mention.
Should not have
• The site should not be flashy or complicated or complex or "busy"

```html
<!DOCTYPE html>
<html lang="en">
<head>
<meta charset="utf-8">
<title>Vornelix Capital</title>
<link rel="stylesheet" href="https://fonts.googleapis.com/css2?family=Raleway:wght@500;600;700;800&family=Lato:wght@400;700&family=Quicksand:wght@400;500;600&display=swap">
<style>
:root{
  --gold:#c69a2c;
  --gold-dark:#b08522;
  --ink:#111111;
  --text:#333333;
  --muted:#666666;
  --light:#eeeeee;
  --field:#efefef;
  --white:#ffffff;
  --footer:#141414;
}
*{margin:0;padding:0;box-sizing:border-box}
html,body{width:1200px;height:2679px;overflow:hidden;background:var(--white)}
body{position:relative;font-family:"Quicksand",sans-serif;color:var(--text)}
.abs{position:absolute}

/* header */
.site-header{position:absolute;left:0;top:0;width:1200px;height:125px;background:var(--white)}
.brand{position:absolute;display:flex;align-items:center;gap:8px;font-family:"Raleway",sans-serif;font-weight:800;color:var(--ink);line-height:1}
.brand-mark{width:12px;height:12px;background:var(--gold)}
.site-header .brand{left:79px;top:50px;font-size:20px;letter-spacing:1px}
.main-nav{position:absolute;top:52px;left:446px;display:flex;font-family:"Quicksand",sans-serif;font-weight:500;font-size:15px;color:var(--ink)}
.main-nav a{color:inherit;text-decoration:none;position:absolute;white-space:nowrap}
.main-nav .active{color:var(--gold)}
.main-nav .active::before{content:"";position:absolute;left:-14px;top:7px;width:6px;height:6px;background:var(--gold);transform:rotate(45deg)}
.nav-divider{position:absolute;left:895px;top:42px;width:3px;height:45px;background:#dddddd}
.call{position:absolute;left:970px;top:42px}
.call-label{font-size:15px;font-weight:500;color:var(--ink)}
.call-number{font-family:"Quicksand",sans-serif;font-size:20px;font-weight:600;color:var(--gold);letter-spacing:1px;margin-top:2px}
.call-icon{position:absolute;left:922px;top:44px}

/* hero */
.hero{position:absolute;left:0;top:125px;width:1200px;height:554px;
  background:linear-gradient(120deg,#1c232b 0%,#3a4550 35%,#2c3844 60%,#1b2a38 100%)}
.hero-title{position:absolute;left:0;width:1200px;top:150px;text-align:center;font-family:"Raleway",sans-serif;font-weight:800;font-size:54px;line-height:64px;color:var(--white)}
.hero-sub{position:absolute;left:0;width:1200px;top:294px;text-align:center;font-family:"Lato",sans-serif;font-weight:700;font-size:21px;color:var(--white)}
.btn{position:absolute;display:flex;align-items:center;justify-content:center;background:var(--gold);color:var(--white);font-family:"Lato",sans-serif;font-size:21px;text-transform:uppercase}
.hero .btn{left:486px;top:338px;width:228px;height:57px}
.hero-arrow{position:absolute;top:245px}

/* welcome */
.welcome{position:absolute;left:0;top:679px;width:1200px;height:489px}
.welcome-accent{position:absolute;left:1027px;top:0;width:173px;height:489px;background:var(--gold)}
.welcome-photo{position:absolute;left:654px;top:77px;width:468px;height:333px;background:linear-gradient(180deg,#3c5a8c 0%,#5a7aa8 45%,#3b3a3a 70%,#7a5a30 100%)}
.eyebrow{font-family:"Lato",sans-serif;font-size:20px;color:var(--gold);text-transform:uppercase}
.welcome .eyebrow{position:absolute;left:79px;top:62px}
.welcome-title{position:absolute;left:79px;top:92px;font-family:"Raleway",sans-serif;font-weight:600;font-size:40px;letter-spacing:1px;color:var(--ink)}
.welcome-copy{position:absolute;left:79px;width:470px;font-size:13.5px;line-height:28px;color:var(--muted)}
.welcome-copy.first{top:147px}
.welcome-copy.second{top:247px}
.welcome .btn{left:77px;top:373px;width:187px;height:52px;font-size:20px}

/* projects */
.projects-head{position:absolute;left:0;top:1168px;width:1200px;height:175px;background:var(--light);text-align:center}
.projects-head .eyebrow{position:absolute;left:0;width:1200px;top:60px}
.section-title{font-family:"Raleway",sans-serif;font-weight:800;font-size:40px;color:var(--ink);text-transform:uppercase}
.projects-head .section-title{position:absolute;left:0;width:1200px;top:92px}
.project-grid{position:absolute;left:0;top:1343px;width:1200px;height:479px;display:grid;grid-template-columns:repeat(4,300px);grid-template-rows:repeat(2,239.5px)}
.project-tile{position:relative}
.tile-overlay{position:absolute;inset:0;background:rgba(20,20,20,.82);text-align:center}
.tile-title{position:absolute;left:0;width:100%;top:72px;font-family:"Lato",sans-serif;font-weight:700;font-size:16px;color:var(--white)}
.tile-sub{position:absolute;left:0;width:100%;top:98px;font-size:13px;color:var(--gold)}
.tile-actions{position:absolute;left:93px;top:136px;display:flex;gap:8px}
.tile-actions span{width:46px;height:46px;border-radius:50%;background:var(--white);display:flex;align-items:center;justify-content:center}
.view-more{position:absolute;left:0;top:1822px;width:1200px;height:94px;background:var(--gold);display:flex;align-items:center;justify-content:center;gap:14px;font-family:"Lato",sans-serif;font-weight:700;font-size:21px;color:var(--white);text-decoration:underline}

/* contact */
.contact{position:absolute;left:0;top:1916px;width:1200px;height:608px;text-align:center}
.contact .eyebrow{position:absolute;left:0;width:1200px;top:62px}
.contact .section-title{position:absolute;left:0;width:1200px;top:94px}
.contact-intro{position:absolute;left:0;width:1200px;top:148px;font-size:14px;font-weight:500;color:var(--ink)}
.info{position:absolute;top:210px;width:300px;text-align:center}
.info-icon{width:60px;height:60px;margin:0 auto;border:2px solid var(--gold);border-radius:50%;display:flex;align-items:center;justify-content:center}
.info-text{margin-top:20px;font-size:13.5px;color:var(--text)}
.field{position:absolute;background:var(--field);border:1px solid #e6e6e6;font-size:13.5px;color:#555;padding:17px 14px;text-align:left}
.contact .btn{left:527px;top:493px;width:146px;height:52px;font-size:20px}

/* footer */
.site-footer{position:absolute;left:0;top:2524px;width:1200px;height:155px;background:var(--footer)}
.site-footer .brand{left:79px;top:68px;font-size:18px;color:var(--white);letter-spacing:1px}
.footer-nav{position:absolute;left:0;width:1200px;top:54px;text-align:center;font-size:13.5px;color:var(--white)}
.footer-nav span.sep{margin:0 14px;color:#888}
.copyright{position:absolute;left:0;width:1200px;top:82px;text-align:center;font-size:13.5px;color:#bbbbbb}
.social{position:absolute;top:52px;width:48px;height:48px;border-radius:50%}
.social.filled{background:var(--gold)}
.social.outline{border:2px solid var(--gold)}
</style>
</head>
<body>

<header class="site-header">
  <div class="brand"><span class="brand-mark"></span>VORNELIX CAPITAL</div>
  <nav class="main-nav">
    <a class="active" style="left:0">HOME</a>
    <a style="left:95px">ABOUT US</a>
    <a style="left:210px">PROJECTS</a>
    <a style="left:320px">CONTACT US</a>
  </nav>
  <div class="nav-divider"></div>
  <svg class="call-icon" width="38" height="38" viewBox="0 0 24 24" aria-hidden="true"><path fill="#c69a2c" d="M6.6 10.8c1.4 2.8 3.8 5.1 6.6 6.6l2.2-2.2c.3-.3.7-.4 1-.2 1.1.4 2.3.6 3.6.6.6 0 1 .4 1 1V20c0 .6-.4 1-1 1C10.6 21 3 13.4 3 4c0-.6.4-1 1-1h3.5c.6 0 1 .4 1 1 0 1.3.2 2.5.6 3.6.1.3 0 .7-.2 1z"/></svg>
  <div class="call">
    <div class="call-label">Call Us Today :</div>
    <div class="call-number">123 456 7890</div>
  </div>
</header>

<section class="hero" role="img" aria-label="Modern apartment building with glass balconies at dusk">
  <svg class="hero-arrow" style="left:30px" width="20" height="46" viewBox="0 0 20 46" aria-hidden="true"><path d="M18 2 L3 23 L18 44" fill="none" stroke="#ffffff" stroke-width="1.5"/></svg>
  <svg class="hero-arrow" style="left:1150px" width="20" height="46" viewBox="0 0 20 46" aria-hidden="true"><path d="M2 2 L17 23 L2 44" fill="none" stroke="#ffffff" stroke-width="1.5"/></svg>
  <h1 class="hero-title">WE PROVIDE SAFE, SECURE<br>RETURNS</h1>
  <p class="hero-sub">Manage Your Investments Easily and Effectivelt</p>
  <a class="btn">Get Free Quote</a>
</section>

<section class="welcome">
  <div class="welcome-accent"></div>
  <div class="welcome-photo" role="img" aria-label="Lit retail building at twilight"></div>
  <p class="eyebrow">Welcome To</p>
  <h2 class="welcome-title">VORNELIX CAPITAL</h2>
  <p class="welcome-copy first">Lorem Ipsum is simply dummy text of the printing and typesetting industry. Lorem Ipsum has been the industry's standard dummy text ever since thes, when an unknown printer</p>
  <p class="welcome-copy second">Lorem Ipsum is simply dummy text of the printing and typesetting industry. Lorem Ipsum has been the industry's standard dummy text ever since the 1500s, when an unknown printer took a galley of type and scrambled it to make a type specimen book.</p>
  <a class="btn">Learn More</a>
</section>

<section class="projects-head">
  <p class="eyebrow">What We Do</p>
  <h2 class="section-title">Our Projects</h2>
</section>

<div class="project-grid">
  <div class="project-tile" role="img" aria-label="Dark modern building" style="background:linear-gradient(160deg,#3a3a3a,#1e1e1e)">
    <div class="tile-overlay">
      <div class="tile-title">LOREM IPSUM TEXT</div>
      <div class="tile-sub">We Provide Safe, Secure Returns</div>
      <div class="tile-actions">
        <span><svg width="20" height="20" viewBox="0 0 24 24" aria-hidden="true"><circle cx="10" cy="10" r="6" fill="none" stroke="#c69a2c" stroke-width="3"/><path d="M15 15 L21 21" stroke="#c69a2c" stroke-width="3"/></svg></span>
        <span><svg width="20" height="20" viewBox="0 0 24 24" aria-hidden="true"><path d="M12 4 V20 M4 12 H20" stroke="#c69a2c" stroke-width="3"/></svg></span>
      </div>
    </div>
  </div>
  <div class="project-tile" role="img" aria-label="Glass office tower" style="background:linear-gradient(180deg,#8fb4dc 0%,#5a7fa8 55%,#4a4f55 100%)"></div>
  <div class="project-tile" role="img" aria-label="Suburban house with lawn" style="background:linear-gradient(180deg,#6aa0d8 0%,#3f4f70 50%,#4d8a2e 100%)"></div>
  <div class="project-tile" role="img" aria-label="Brick apartment block" style="background:linear-gradient(180deg,#7eaedc 0%,#a0634c 45%,#7a4a3a 100%)"></div>
  <div class="project-tile" role="img" aria-label="Dark residential block" style="background:linear-gradient(180deg,#9dc2e6 0%,#3e3a36 45%,#5a5650 100%)"></div>
  <div class="project-tile" role="img" aria-label="Blue glass office building" style="background:linear-gradient(180deg,#a8d0f0 0%,#4f8fc0 50%,#8a9aa4 100%)"></div>
  <div class="project-tile" role="img" aria-label="Lit retail building at twilight" style="background:linear-gradient(180deg,#3c5a8c 0%,#2e3440 55%,#7a5a30 100%)"></div>
  <div class="project-tile" role="img" aria-label="White commercial building with parking" style="background:linear-gradient(180deg,#6aa6e0 0%,#e2e6ea 50%,#8c9096 100%)"></div>
</div>

<a class="view-more">VIEW MORE
  <svg width="34" height="16" viewBox="0 0 34 16" aria-hidden="true"><path d="M0 8 H30 M23 1 L31 8 L23 15" fill="none" stroke="#ffffff" stroke-width="3"/></svg>
</a>

<section class="contact">
  <p class="eyebrow">Keep In Touch</p>
  <h2 class="section-title">Contact Us</h2>
  <p class="contact-intro">If you Need an have Question Please Contact Us Today !</p>

  <div class="info" style="left:166px">
    <div class="info-icon"><svg width="24" height="28" viewBox="0 0 24 28" aria-hidden="true"><path d="M12 2a8 8 0 0 0-8 8c0 6 8 16 8 16s8-10 8-16a8 8 0 0 0-8-8z" fill="none" stroke="#c69a2c" stroke-width="2.5"/><circle cx="12" cy="10" r="3" fill="#c69a2c"/></svg></div>
    <div class="info-text">101 - lorem ipsum simple text</div>
  </div>
  <div class="info" style="left:450px">
    <div class="info-icon"><svg width="26" height="26" viewBox="0 0 24 24" aria-hidden="true"><path fill="#c69a2c" d="M6.6 10.8c1.4 2.8 3.8 5.1 6.6 6.6l2.2-2.2c.3-.3.7-.4 1-.2 1.1.4 2.3.6 3.6.6.6 0 1 .4 1 1V20c0 .6-.4 1-1 1C10.6 21 3 13.4 3 4c0-.6.4-1 1-1h3.5c.6 0 1 .4 1 1 0 1.3.2 2.5.6 3.6.1.3 0 .7-.2 1z"/></svg></div>
    <div class="info-text">+1 123 456 7890</div>
  </div>
  <div class="info" style="left:725px">
    <div class="info-icon"><svg width="28" height="28" viewBox="0 0 28 28" aria-hidden="true"><circle cx="14" cy="14" r="13" fill="#c69a2c"/><rect x="7" y="9" width="14" height="10" fill="#ffffff"/><path d="M7 9 L14 15 L21 9" fill="none" stroke="#c69a2c" stroke-width="1.5"/></svg></div>
    <div class="info-text">info@vornelix.com</div>
  </div>

  <div class="field" style="left:182px;top:331px;width:272px;height:50px">Name *</div>
  <div class="field" style="left:464px;top:331px;width:272px;height:50px">Phone *</div>
  <div class="field" style="left:746px;top:331px;width:270px;height:50px">Email *</div>
  <div class="field" style="left:182px;top:392px;width:834px;height:94px">Message *</div>
  <a class="btn">Submit</a>
</section>

<footer class="site-footer">
  <div class="brand"><span class="brand-mark"></span>VORNELIX CAPITAL</div>
  <div class="footer-nav">Home<span class="sep">|</span>About Us<span class="sep">|</span>Projects<span class="sep">|</span>Contact Us</div>
  <div class="copyright">©VORNELIX CAPITAL - 2018 All Right Reserved.</div>
  <div class="social filled" style="left:967px" aria-label="Social link"></div>
  <div class="social outline" style="left:1021px" aria-label="Social link"></div>
  <div class="social outline" style="left:1074px" aria-label="Social link"></div>
</footer>

</body>
</html>
```